Trendy eye catching business card for lawn mowing business

Turf Tidy, a local community lawn mowing service, requires an eye catching trendy business card to drop into letterboxes.

We could simply throw something together from a Microsoft Word template, but we are wanting something more than this. Some other business’ images are attached for some inspiration.

We are requiring the card to have Turf Tidy with our slogan, Call The Brindles. In addition, provide details with that we are a local, affordable lawn mowing service, and for other gardening matters to simply just ask!
Plus the relevant contact details, phone, email, social media.

Target Market(s)

Local community members who require assistance with their garden care

Industry/Entity Type

Gardening

Contact Information for Business Card

the name TURF TIDY is our logo
telephone logo 0438 215 967
email logo turftidy@postbox-mail.example
Instagram logo turftidy
Facebook logo turftidy.sth
Lawn Mowing Service
Local Affordable
edge trim, blow and clipping removal included.
Other gardening matters, just ask!

Font styles to use
Serif
Sans Serif
Decorative
Script

Colors
9bcb3c
ffffff

Requirements
Must have
• All the details listed in Business Card Details.
Make these words prominent:
Turf Tidy
Lawn Mowing Service
Local
Affordable
Nice to have
• Our slogan ‘Call The Brindles’ incorporated.
Different colour background for front and reverse side
Greens, white and black colours
Subtle grass blades images incorporated
Should not have
• No images of lawnmowers.
No images of men/cartoons.
No using initials for Turf Tidy

```html
<!DOCTYPE html>
<html lang="en">
<head>
<meta charset="utf-8">
<title>Turf Tidy – Business Card</title>
<link rel="stylesheet" href="https://fonts.googleapis.com/css2?family=Montserrat:wght@400;500;700;800&family=Quicksand:wght@400&display=swap">
<style>
  :root {
    --page: #e6e6e4;
    --card-dark: #222222;
    --card-light: #ffffff;
    --green: #8cc540;
    --white: #ffffff;
    --ink: #1a1a1a;
    --grey: #777777;
    --rule: #8a8a8a;
  }
  * { box-sizing: border-box; margin: 0; padding: 0; }
  html, body { width: 1200px; height: 1015px; overflow: hidden; }
  body {
    background: var(--page);
    font-family: "Montserrat", Arial, sans-serif;
    position: relative;
  }
  .card {
    position: absolute;
    width: 620px;
    height: 354px;
    overflow: hidden;
    box-shadow: 0 10px 28px rgba(0,0,0,.18);
  }
  .card--front { left: 90px; top: 90px; background: var(--card-dark); }
  .card--back  { left: 490px; top: 570px; background: var(--card-light); }

  .grass {
    position: absolute;
    border-radius: 60% 60% 0 0;
  }
  .card--front .grass--left {
    left: 24px; bottom: 0; width: 160px; height: 130px;
    background: linear-gradient(to top, var(--green) 10%, rgba(140,197,64,0.15));
  }
  .card--front .grass--right {
    right: 0; bottom: 0; width: 100px; height: 220px;
    background: linear-gradient(to top, var(--green) 10%, rgba(140,197,64,0.15));
  }
  .card--back .grass--left {
    left: 20px; bottom: 14px; width: 250px; height: 300px;
    background: linear-gradient(to top, var(--green) 20%, rgba(140,197,64,0.1));
  }

  .front-copy {
    position: absolute; left: 60px; width: 420px; top: 46px;
    text-align: center; color: var(--white);
  }
  .front-copy .service { font-weight: 800; font-size: 26px; letter-spacing: 1px; white-space: nowrap; }
  .front-copy .promise { font-weight: 500; font-size: 24px; color: var(--green); margin-top: 2px; }
  .front-copy .details { font-size: 14px; line-height: 1.35; margin-top: 10px; }
  .front-copy .phone {
    font-family: "Quicksand", Arial, sans-serif; font-size: 30px;
    color: var(--green); letter-spacing: 2px; margin-top: 4px;
  }

  .brand { position: absolute; text-align: center; }
  .brand .name { font-weight: 800; color: var(--green); line-height: 1; white-space: nowrap; }
  .brand .slogan {
    display: flex; align-items: center; gap: 8px;
    font-weight: 700; color: var(--grey); letter-spacing: 3px; white-space: nowrap;
  }
  .brand .slogan::before, .brand .slogan::after {
    content: ""; flex: 1; height: 1px; background: var(--rule);
  }
  .card--front .brand { left: 196px; top: 262px; width: 300px; }
  .card--front .brand .name { font-size: 44px; }
  .card--front .brand .slogan { font-size: 12px; margin-top: 4px; }

  .card--back .brand { left: 290px; top: 50px; width: 310px; }
  .card--back .brand .name { font-size: 50px; }
  .card--back .brand .slogan { font-size: 14px; margin-top: 6px; }

  .contacts {
    position: absolute; left: 330px; top: 170px;
    list-style: none; color: var(--ink); font-size: 15px;
  }
  .contacts li { display: flex; align-items: center; gap: 8px; margin-bottom: 7px; }
  .contacts li.gap { margin-top: 10px; }
  .contacts svg { width: 17px; height: 17px; flex: none; }
  .green-band {
    position: absolute; left: 0; right: 0; bottom: 0; height: 14px; background: var(--green);
  }
</style>
</head>
<body>

<section class="card card--front" aria-label="Card front">
  <div class="grass grass--left" role="img" aria-label="Green grass blades"></div>
  <div class="grass grass--right" role="img" aria-label="Green grass blades"></div>
  <div class="front-copy">
    <p class="service">LAWN MOWING SERVICE</p>
    <p class="promise">Local. Affordable.</p>
    <p class="details">Edge trim, blow and clipping removal included.<br>Other gardening matters, just ask!</p>
    <p class="phone">0438 215 967</p>
  </div>
  <div class="brand">
    <p class="name">TURF TIDY</p>
    <p class="slogan">CALL THE BRINDLES</p>
  </div>
</section>

<section class="card card--back" aria-label="Card back">
  <div class="grass grass--left" role="img" aria-label="Tall green grass blades"></div>
  <div class="brand">
    <p class="name">TURF TIDY</p>
    <p class="slogan">CALL THE BRINDLES</p>
  </div>
  <ul class="contacts">
    <li>
      <svg viewBox="0 0 20 20" aria-hidden="true"><rect x="1" y="1" width="18" height="18" rx="3" fill="none" stroke="#8cc540" stroke-width="1.6"/><path d="M6 5c-1 1-1 3 1 6s4 4 6 4l1-2-2-1-1 1c-1-.5-2-1.5-3-3l1-1-1-2z" fill="#8cc540"/></svg>
      0438 215 967
    </li>
    <li>
      <svg viewBox="0 0 20 20" aria-hidden="true"><rect x="1" y="4" width="18" height="12" fill="#8cc540"/><path d="M1 4l9 7 9-7" fill="none" stroke="#fff" stroke-width="1.4"/></svg>
      turftidy@postbox-mail.example
    </li>
    <li class="gap">
      <svg viewBox="0 0 20 20" aria-hidden="true"><circle cx="10" cy="10" r="8.5" fill="none" stroke="#8cc540" stroke-width="1.6"/></svg>
      pics.example/turftidy
    </li>
    <li>
      <svg viewBox="0 0 20 20" aria-hidden="true"><circle cx="10" cy="10" r="8.5" fill="none" stroke="#8cc540" stroke-width="1.6"/></svg>
      page.example/turftidy.sth
    </li>
  </ul>
  <div class="green-band"></div>
</section>

</body>
</html>
```